Boutique Store Selling Antiques and Unique Finds

I need a Web Page designed for my Store Called "Willow Lane". I would like a very classic, muted design that looks European when pulled up. I will be selling Antiques from all over the world and Unique finds that have reproduced. I will also be selling high-end purses and jewelry with unique, reasonable products for the every-day buyer as well.

Target Market(s)

25-70 year old men and women;)

Coding

Coded - Design and coding required

Number of Pages Required

1 page

Colors

Designer to choose only greyscale colors for use in the design.

Requirements
Must have
• I want it

```html
<!DOCTYPE html>
<html lang="en">
<head>
<meta charset="utf-8">
<title>Willow Lane — Antiques and Unique Finds</title>
<link href="https://fonts.googleapis.com/css2?family=Lato:wght@400;700;900&display=swap" rel="stylesheet">
<style>
:root{
  --ink:#111;
  --text:#444;
  --muted:#666;
  --line:#bdbdbd;
  --panel:#efefef;
  --white:#fff;
  --footer:#232323;
  --footer-text:#d8d8d8;
  --btn:#141414;
}
*{box-sizing:border-box;margin:0;padding:0}
html,body{width:1200px;height:3879px;overflow:hidden;background:var(--white)}
body{position:relative;font-family:'Lato',sans-serif;color:var(--text)}
.abs{position:absolute}
.center{text-align:center}

/* header */
.ship{left:94px;top:46px;font-size:11px;color:var(--ink);display:flex;gap:6px;align-items:center}
.brand-rule{top:98px;height:1px;background:var(--line)}
.brand{left:0;width:1200px;top:80px;text-align:center;font-size:28px;letter-spacing:6px;color:var(--ink);font-weight:400}
.brand-mark{left:591px;top:38px;width:18px;height:18px;background:var(--ink)}
.tools{right:74px;top:40px;display:flex;gap:16px;align-items:center;font-size:12px;color:var(--ink)}
.cart-dot{width:26px;height:26px;border-radius:50%;background:var(--ink);display:flex;align-items:center;justify-content:center}
.nav{left:0;width:1200px;top:137px;display:flex;justify-content:center;gap:32px;font-size:15px;font-weight:700;color:var(--ink)}
.nav-rule{top:173px;left:0;width:1200px;height:2px;background:#ddd}

/* hero */
.hero{top:176px;left:0;width:1200px;height:559px;background:linear-gradient(180deg,#6d5a3c 0,#8a6f45 70px,#3a3530 130px,#cfc6ba 200px,#ddd6cb 380px,#4a4642 460px,#2d2a27 559px)}
.hero-photo{left:600px;top:176px;width:480px;height:559px;background:radial-gradient(ellipse at 50% 45%,#b8925c 0,#8a6a3e 35%,rgba(80,70,60,0) 70%)}
.hero h1{left:74px;top:380px;font-size:56px;font-weight:900;color:var(--ink);letter-spacing:1px}
.hero-sub{left:75px;top:455px;font-size:20px;color:var(--ink);line-height:25px}
.btn{background:var(--btn);color:var(--white);font-size:14px;font-weight:700;display:flex;align-items:center;justify-content:center;letter-spacing:.3px}
.dots{display:flex;gap:8px}
.dot{width:13px;height:13px;border-radius:50%;background:#999}
.dot.on{background:var(--white)}

/* sections */
.title{left:0;width:1200px;text-align:center;font-size:19px;font-weight:700;color:var(--ink)}
.photo{position:absolute}
.label{position:absolute;text-align:center;font-size:14px;color:var(--ink);letter-spacing:.3px}
.price{position:absolute;text-align:center;font-size:17px;font-weight:700;color:var(--ink)}
.arrow{position:absolute;width:20px;height:30px}
.rule{left:75px;width:1051px;height:2px;background:#ccc}
.body-copy{font-size:14px;line-height:27.5px;color:var(--muted);text-align:center}
.card{background:var(--white)}
.card h2{font-size:19px;font-weight:700;color:var(--ink);text-align:center}

/* reviews */
.review{width:336px;font-size:14px;line-height:25px;color:var(--muted)}
.review b{display:block;color:var(--ink);margin-top:8px;font-size:14px}
.rdot{width:11px;height:11px;border-radius:50%;background:#999}
.rdot.on{background:var(--ink)}

/* footer */
.footer{top:3521px;left:0;width:1200px;height:358px;background:var(--footer)}
.f-brand{left:75px;top:3608px;font-size:21px;letter-spacing:4px;color:var(--white)}
.f-mark{left:176px;top:3584px;width:14px;height:14px;background:var(--white)}
.f-about{left:75px;top:3660px;width:250px;font-size:14px;line-height:28px;color:var(--footer-text)}
.f-col h3{font-size:14px;font-weight:700;color:var(--white);margin-bottom:7px;letter-spacing:.3px}
.f-col li{list-style:none;font-size:14px;line-height:31.5px;color:var(--footer-text)}
.f-col.cs li{line-height:27.5px}
.email{left:794px;top:3622px;width:242px;height:38px;background:var(--white);font-size:13px;color:#333;padding-left:14px;display:flex;align-items:center}
.signup{left:1050px;top:3622px;width:76px;height:38px;background:#3a3a3a;color:var(--white);font-size:11px;display:flex;align-items:center;justify-content:center}
.social{left:794px;top:3726px;display:flex;gap:17px}
.social span{width:16px;height:16px;border-radius:50%;background:var(--white);display:block}
.copy{left:794px;top:3781px;font-size:11px;line-height:21px;color:var(--footer-text)}
</style>
</head>
<body>

<!-- header -->
<div class="abs ship">
  <svg width="12" height="9" viewBox="0 0 12 9"><rect x="0" y="1" width="7" height="5" fill="#111"/><path d="M7 3h3l2 2v1H7z" fill="#111"/><circle cx="3" cy="7.5" r="1.4" fill="#111"/><circle cx="9.5" cy="7.5" r="1.4" fill="#111"/></svg>
  FREE SHIPPING ON ORDER OVER $50
</div>
<div class="abs brand-mark"></div>
<div class="abs brand-rule" style="left:75px;width:355px"></div>
<div class="abs brand-rule" style="left:767px;width:359px"></div>
<div class="abs brand">WILLOW LANE</div>
<div class="abs tools">
  <svg width="13" height="13" viewBox="0 0 13 13"><circle cx="5.5" cy="5.5" r="4" fill="none" stroke="#111" stroke-width="2"/><path d="M8.5 8.5l3.5 3.5" stroke="#111" stroke-width="2"/></svg>
  <svg width="12" height="13" viewBox="0 0 12 13"><circle cx="6" cy="4" r="3" fill="#111"/><path d="M0 13c0-4 3-6 6-6s6 2 6 6z" fill="#111"/></svg>
  <svg width="11" height="13" viewBox="0 0 11 13"><path d="M2.5 6V4a3 3 0 016 0v2" fill="none" stroke="#111" stroke-width="1.6"/><rect x="0.5" y="6" width="10" height="7" fill="#111"/></svg>
  <svg width="14" height="12" viewBox="0 0 14 12"><path d="M7 12L1 6A3.3 3.3 0 017 2a3.3 3.3 0 016 4z" fill="#111"/></svg>
  <span style="display:flex;align-items:center;gap:8px"><span class="cart-dot"><svg width="12" height="10" viewBox="0 0 12 10"><path d="M0 1h2l2 6h6l1.5-4.5H3" fill="none" stroke="#fff" stroke-width="1.4"/><circle cx="5" cy="9" r="1" fill="#fff"/><circle cx="9" cy="9" r="1" fill="#fff"/></svg></span>CART</span>
</div>
<nav class="abs nav">
  <span>HOME</span><span>ONLINE SHOP</span><span>PRODUCTS</span><span>ABOUT US</span><span>BLOG</span><span>REVIEWS</span><span>CONTACT US</span>
</nav>
<div class="abs nav-rule"></div>

<!-- hero -->
<section>
  <div class="abs hero" role="img" aria-label="Antique jewelled crown on a pedestal beneath an ornate gilt frame"></div>
  <div class="abs hero-photo" role="img" aria-label="Ornate gold crown with blue stones"></div>
  <div class="hero"></div>
  <h1 class="abs" style="left:74px;top:380px;font-size:56px;font-weight:900;color:var(--ink);letter-spacing:1px">WILLOW LANE</h1>
  <p class="abs hero-sub">We are a Boutique Store Selling Antiques<br>and Unique Finds.</p>
  <div class="abs btn" style="left:77px;top:526px;width:152px;height:51px">SHOP NOW</div>
  <div class="abs dots" style="left:580px;top:681px"><span class="dot on"></span><span class="dot"></span></div>
</section>

<!-- featured collections -->
<section>
  <h2 class="abs title" style="top:791px">FEATURED COLLECTIONS</h2>
  <svg class="arrow" style="left:45px;top:965px" viewBox="0 0 20 30"><path d="M15 2L4 15l11 13" fill="none" stroke="#555" stroke-width="2"/></svg>
  <svg class="arrow" style="left:1138px;top:965px" viewBox="0 0 20 30"><path d="M5 2l11 13L5 28" fill="none" stroke="#555" stroke-width="2"/></svg>

  <div class="photo" style="left:75px;top:855px;width:240px;height:240px;background:radial-gradient(circle at 50% 60%,#8a6a20 0,#2a2015 45%,#0d0b0a 80%)" role="img" aria-label="Gold crown on dark velvet"></div>
  <div class="photo" style="left:345px;top:855px;width:241px;height:240px;background:linear-gradient(160deg,#6b4a30,#3a2a20 50%,#a89a8a)" role="img" aria-label="Antique jewellery chest with pearls and pocket watch"></div>
  <div class="photo" style="left:616px;top:855px;width:241px;height:240px;background:radial-gradient(circle at 50% 50%,#a07828 0,#3a2a10 30%,#000 55%)" role="img" aria-label="Jewelled gold crown on black"></div>
  <div class="photo" style="left:889px;top:855px;width:236px;height:240px;background:radial-gradient(circle at 55% 45%,#9a7a40 0,#4a3520 40%,#1a130d 80%)" role="img" aria-label="Brass antique mantel clock"></div>

  <div class="label" style="left:75px;top:1120px;width:240px">SED VEL URNA LIGULA</div>
  <div class="label" style="left:345px;top:1120px;width:241px">SED VEL URNA LIGULA</div>
  <div class="label" style="left:616px;top:1120px;width:241px">SED VEL URNA LIGULA</div>
  <div class="label" style="left:889px;top:1120px;width:236px">SED VEL URNA LIGULA</div>
</section>

<div class="abs rule" style="top:1198px"></div>

<!-- featured products -->
<section>
  <h2 class="abs title" style="top:1253px">FEATURED PRODUCTS</h2>
  <svg class="arrow" style="left:45px;top:1478px" viewBox="0 0 20 30"><path d="M15 2L4 15l11 13" fill="none" stroke="#555" stroke-width="2"/></svg>
  <svg class="arrow" style="left:1138px;top:1478px" viewBox="0 0 20 30"><path d="M5 2l11 13L5 28" fill="none" stroke="#555" stroke-width="2"/></svg>

  <div class="photo" style="left:75px;top:1318px;width:239px;height:211px;background:radial-gradient(ellipse at 50% 50%,#8a9a6a 0,#c8c0a0 18%,#f5f5f5 32%)" role="img" aria-label="Cloisonné enamel vase"></div>
  <div class="photo" style="left:346px;top:1318px;width:240px;height:211px;background:radial-gradient(ellipse at 50% 50%,#fff 0,#fff 22%,#8a8070 30%,#f5f5f5 45%)" role="img" aria-label="Vintage television set"></div>
  <div class="photo" style="left:617px;top:1318px;width:239px;height:211px;background:radial-gradient(circle at 40% 45%,#6aa8a0 0,#b09a60 25%,#d8d0c0 55%,#e8e4dc)" role="img" aria-label="Vintage brooches and pearl strands"></div>
  <div class="photo" style="left:888px;top:1318px;width:238px;height:211px;background:radial-gradient(circle at 50% 52%,#fff 0,#eee 16%,#8a5a30 24%,#f5f5f5 36%)" role="img" aria-label="Antique pocket watch"></div>

  <div class="label" style="left:75px;top:1557px;width:239px">SED VEL URNA LIGULA</div>
  <div class="label" style="left:346px;top:1557px;width:240px">SED VEL URNA LIGULA</div>
  <div class="label" style="left:617px;top:1557px;width:239px">SED VEL URNA LIGULA</div>
  <div class="label" style="left:888px;top:1557px;width:238px">SED VEL URNA LIGULA</div>
  <div class="price" style="left:75px;top:1584px;width:239px">$259.00</div>
  <div class="price" style="left:346px;top:1584px;width:240px">$259.00</div>
  <div class="price" style="left:617px;top:1584px;width:239px">$259.00</div>
  <div class="price" style="left:888px;top:1584px;width:238px">$259.00</div>
</section>

<!-- what's on -->
<section>
  <div class="abs" style="left:587px;top:1682px;width:613px;height:530px;background:var(--panel)"></div>
  <div class="photo" style="left:0;top:1682px;width:587px;height:530px;background:radial-gradient(ellipse at 40% 50%,#5a4a30 0,#3a3020 35%,#a89a88 70%,#c8bfb2)" role="img" aria-label="Antique bronze crown with coloured stones"></div>
  <div class="abs card" style="left:434px;top:1768px;width:692px;height:358px">
    <h2 style="margin-top:64px">WHAT'S ON</h2>
    <p class="body-copy" style="margin-top:11px">Cras non dolor eu nisi dignissim pretium. Praesent neque arcu, commodo et suscipit ut,<br>bibendum non ipsum. Nam fringilla mattis&nbsp; bibendum&nbsp; id maximus nibh.<br>Neque porro quisquam est, qui dolorem ipsum quia dolor sit amet, consectetur, adipisci<br>velit, sed quia non numquam eius modi</p>
  </div>
  <div class="abs btn" style="left:703px;top:2006px;width:152px;height:51px">READ MORE</div>
</section>

<!-- about -->
<section>
  <h2 class="abs title" style="top:2270px">ABOUT WILLOW LANE</h2>
  <p class="abs body-copy" style="left:60px;width:1080px;top:2309px">Sed ut perspiciatis unde omnis iste natus error sit voluptatem accusantium doloremque laudantium, totam rem aperiam, eaque ipsa quae ab illo inventore<br>veritatis et quasi architecto beatae vitae dicta sunt explicabo. Nemo enim ipsam voluptatem quia voluptas sit aspernatur aut odit aut fugit,<br>sed quia consequuntur magni dolores eos qui ratione voluptatem sequi nesciunt. Neque porro quisquam est, qui dolorem ipsum quia dolor sit amet,<br>consectetur, adipisci velit, sed quia non numquam eius modi tempora incidunt ut labore.</p>
  <div class="abs btn" style="left:524px;top:2447px;width:152px;height:50px">READ MORE</div>
</section>

<!-- discover -->
<section>
  <div class="abs" style="left:0;top:2577px;width:613px;height:530px;background:var(--panel)"></div>
  <div class="photo" style="left:613px;top:2577px;width:587px;height:530px;background:linear-gradient(180deg,#c8bca8 0,#8a6a3a 35%,#6a5030 60%,#3a2a20 80%,#5a2a25)" role="img" aria-label="Gilt star crown resting on a stack of old books"></div>
  <div class="abs card" style="left:75px;top:2663px;width:693px;height:358px">
    <h2 style="margin-top:64px">DISCOVER</h2>
    <p class="body-copy" style="margin-top:11px">Cras non dolor eu nisi dignissim pretium. Praesent neque arcu, commodo et suscipit ut,<br>bibendum non ipsum. Nam fringilla mattis&nbsp; bibendum&nbsp; id maximus nibh.<br>Neque porro quisquam est, qui dolorem ipsum quia dolor sit amet, consectetur, adipisci<br>velit, sed quia non numquam eius modi</p>
  </div>
  <div class="abs btn" style="left:345px;top:2900px;width:152px;height:52px">READ MORE</div>
</section>

<!-- reviews -->
<section>
  <h2 class="abs title" style="top:3169px">REVIEWS</h2>
  <div class="abs review" style="left:75px;top:3221px">“ Sed ut perspiciatis unde omnis iste natus error sit voluptatem accusantium doloremque laudantium, totam rem aperiam, eaque ipsa quae ab illo inventore veritatis et quasi architecto beatae vitae dicta sunt explicabo..”<b>– Aubrey</b></div>
  <div class="abs review" style="left:434px;top:3221px">“ Sed ut perspiciatis unde omnis iste natus error sit voluptatem accusantium doloremque laudantium, totam rem aperiam, eaque ipsa quae ab illo inventore veritatis et quasi architecto beatae vitae dicta sunt explicabo..”<b>– Aubrey</b></div>
  <div class="abs review" style="left:795px;top:3221px">“ Sed ut perspiciatis unde omnis iste natus error sit voluptatem accusantium doloremque laudantium, totam rem aperiam, eaque ipsa quae ab illo inventore veritatis et quasi architecto beatae vitae dicta sunt explicabo..”<b>– Aubrey</b></div>
  <div class="abs dots" style="left:563px;top:3436px;gap:10px"><span class="rdot on"></span><span class="rdot"></span><span class="rdot"></span><span class="rdot"></span></div>
</section>

<!-- footer -->
<footer>
  <div class="abs footer"></div>
  <div class="abs f-mark"></div>
  <div class="abs f-brand">WILLOW LANE</div>
  <p class="abs f-about">Cras non dolor eu nisi dignissim pretium. Praesent neque arcu, commodo et suscipit ut, bibendum non ipsum.</p>
  <div class="abs f-col" style="left:364px;top:3582px">
    <h3>NAVIGATION</h3>
    <ul><li>Home</li><li>Online Shop</li><li>Products</li><li>About Us</li><li>Blog</li><li>Reviews</li><li>Contact Us</li></ul>
  </div>
  <div class="abs f-col cs" style="left:553px;top:3582px">
    <h3>CUSTOMER SERVICE</h3>
    <ul><li>Sed ut perspiciatis</li><li>Unde omnis iste</li><li>Natus error</li><li>Sit voluptatem</li><li>Accusantium doloremque</li></ul>
  </div>
  <div class="abs f-col" style="left:794px;top:3582px"><h3>NEWSLETTER SIGN UP</h3></div>
  <div class="abs email">Enter Email Address</div>
  <div class="abs signup">SIGN UP</div>
  <div class="abs f-col" style="left:794px;top:3695px"><h3>FOLLOW US</h3></div>
  <div class="abs social"><span></span><span></span><span></span><span></span><span></span></div>
  <p class="abs copy">Copyright © 2021. Company Name<br>All Right Reserved</p>
</footer>

</body>
</html>
```